BildeVOLD buisnesscard

Hey :) I need a modern buisnesscard for my company BildeVOLD
It most have:
Dagligleder og Fotograf: Henrik Audun Strandvik

Mob: +4791264085
Epost: post@bildevold.example
Adresse: Kvernbakken9, 6040 Fjordvik

Facbook and instagram logo with text BildeVOLD

BildeVOLD logo

It Company

```html
<!DOCTYPE html>
<html lang="no">
<head>
<meta charset="utf-8">
<title>BildeVOLD – business card</title>
<link rel="stylesheet" href="https://fonts.googleapis.com/css2?family=Roboto:wght@400&family=Saira+Semi+Condensed:wght@600;700&display=swap">
<style>
  :root {
    --backdrop: #e4e4e4;
    --card-dark: #0b0b0d;
    --card-light: #fbfbfb;
    --brand-blue: #1a7dc3;
    --brand-pink: #d4237a;
    --text-grey: #4a4a4a;
    --rule-grey: #6d6d6d;
  }
  * { margin: 0; padding: 0; box-sizing: border-box; }
  html, body {
    width: 1200px; height: 576px; overflow: hidden;
    background: var(--backdrop);
  }
  .canvas { position: relative; width: 1200px; height: 576px; }

  .card {
    position: absolute; top: 138px; width: 484px; height: 293px;
    box-shadow: 0 2px 5px rgba(0,0,0,.25);
  }
  .card--front { left: 81px; background: var(--card-dark); }
  .card--back { left: 602px; background: var(--card-light); }

  .wordmark {
    font-family: "Saira Semi Condensed", sans-serif;
    font-weight: 700; color: var(--brand-blue);
    letter-spacing: .5px; line-height: 1; white-space: nowrap;
  }
  .brand-square { background: var(--brand-pink); }

  /* front */
  .front-lockup {
    position: absolute; left: 0; right: 0; top: 94px;
    display: flex; flex-direction: column; align-items: center; gap: 14px;
  }
  .front-lockup .brand-square { width: 72px; height: 72px; }
  .front-lockup .wordmark { font-size: 38px; }

  /* back */
  .back-lockup {
    position: absolute; left: 24px; top: 34px;
    display: flex; align-items: center;
  }
  .back-lockup .brand-square { width: 44px; height: 44px; }
  .back-lockup .divider {
    width: 1px; height: 56px; background: #9a9a9a; margin: 0 14px 0 15px;
  }
  .back-lockup .wordmark { font-size: 34px; }

  .holder {
    position: absolute; right: 25px; top: 152px; text-align: right;
  }
  .holder-name {
    font-family: "Saira Semi Condensed", sans-serif; font-weight: 600;
    font-size: 19px; color: var(--brand-blue); line-height: 1; white-space: nowrap;
  }
  .holder-role {
    margin-top: 6px;
    font-family: "Roboto", sans-serif; font-size: 11.5px; color: var(--text-grey);
    white-space: nowrap;
  }
  .holder-rule {
    position: absolute; left: 25px; top: 190px; width: 238px; height: 1px;
    background: var(--rule-grey);
  }

  .contact-list {
    position: absolute; left: 26px; top: 211px; list-style: none;
    font-family: "Roboto", sans-serif; font-size: 12.5px; color: var(--text-grey);
  }
  .contact-list li { display: flex; align-items: center; height: 17px; white-space: nowrap; }
  .contact-list svg { width: 11px; height: 11px; margin-right: 12px; fill: var(--brand-blue); }

  .online {
    position: absolute; right: 25px; top: 224px; text-align: right;
    font-family: "Roboto", sans-serif; font-size: 12.5px; color: var(--text-grey);
    white-space: nowrap;
  }
  .online-social {
    margin-top: 6px; display: flex; align-items: center; justify-content: flex-end; gap: 6px;
  }
  .online-social .brand-square { width: 13px; height: 13px; background: var(--brand-blue); }
</style>
</head>
<body>
<main class="canvas">

  <section class="card card--front" aria-label="Card front">
    <div class="front-lockup">
      <span class="brand-square" aria-hidden="true"></span>
      <span class="wordmark">BildeVOLD</span>
    </div>
  </section>

  <section class="card card--back" aria-label="Card back">
    <div class="back-lockup">
      <span class="brand-square" aria-hidden="true"></span>
      <span class="divider" aria-hidden="true"></span>
      <span class="wordmark">BildeVOLD</span>
    </div>

    <div class="holder">
      <p class="holder-name">Henrik Audun Strandvik</p>
      <p class="holder-role">Managing Director &amp; Photographer</p>
    </div>
    <div class="holder-rule" aria-hidden="true"></div>

    <ul class="contact-list">
      <li>
        <svg viewBox="0 0 12 12" aria-hidden="true"><path d="M3 0h6a1 1 0 0 1 1 1v10a1 1 0 0 1-1 1H3a1 1 0 0 1-1-1V1a1 1 0 0 1 1-1zm.5 1.5v8h5v-8zM6 10a.6.6 0 1 0 0 1.2A.6.6 0 0 0 6 10z"/></svg>
        +4791264085
      </li>
      <li>
        <svg viewBox="0 0 12 12" aria-hidden="true"><path d="M0 2.5h12v7H0zM1 3.3v.4l5 3.2 5-3.2v-.4zM1 4.9V8.7h10V4.9L6 8z"/></svg>
        post@bildevold.example
      </li>
      <li>
        <svg viewBox="0 0 12 12" aria-hidden="true"><path d="M6 0a4 4 0 0 1 4 4c0 3-4 8-4 8S2 7 2 4a4 4 0 0 1 4-4zm0 2.4A1.6 1.6 0 1 0 6 5.6 1.6 1.6 0 0 0 6 2.4z"/></svg>
        Kvernbakken9, 6040 Fjordvik
      </li>
    </ul>

    <div class="online">
      <p>www.bildevold.example</p>
      <p class="online-social"><span class="brand-square" aria-hidden="true"></span>/BildeVOLD</p>
    </div>
  </section>

</main>
</body>
</html>
```